Form Sculptors Business Card

Professional cosmetic surgery company, based in very exclusive area in London. High profiled clientele. Brand is very artistic, modern, state-of-the-art, safe. The best in the business. Celebrity clientele.

Form Sculptor’s of London is a brand serving a discriminating and exclusive clientele who value personal service that is both intimate and high end. Our clients choose Form Sculptors because of the relationships we share with all of our customers. The clients of Form Sculptors have an equal partnership between customers, and very experienced, highly qualified medical professionals. This together provides you with a professional service that keeps you looking good and feeling good. It is a relationship based on honesty, compassion, loyalty and respect.
Form Sculptor’s have provided services for internationally recognised celebrities, and other high profiled individuals.

The cards are used for networking at private, exclusive events with VIPs.

Target Market(s)

Professionals
Rich people

Industry/Entity Type

Professional Service

Contact Information for Business Card

Need double sided business card design for 4 people. Back of the business card needs to have contrast background to the front with butterfly watermark with services provided:
Hair Restoration surgery
Hair Loss treatments
Breast surgery
Rhinoplasty
Pulvix Liposuction
Fat Grafting
Lumaxin & Fillers

Front of the business card needs to be a nice satin black.
with following information:
Calvert Osterlund - name
Chief Executive - Job title

www.formsculptors-example.co.uk
calvert@formsculptors-example.co.uk
Phone: +44 (0)207 946 0321
Mobile: +44 (0)7700 900 147

The London Farrowmere Clinic
14 Farrowmere Lane | London | W1X 4QP
Off Quenby Street

All business cards have the same address, phone, website as Calvert's details.
Same details on the back of the business card as well.
The other cards have different name, job title, email, mobile number

Teodor Lunn - Name
Partner - Job Title
Former England International Cricketer - please include below job title

email: teodor@formsculptors-example.co.uk
mobile: +44(0)7700 900582

Dr Castello Vranesk - Name
Plastic Surgeon - Job Title
drvranesk@formsculptors-example.co.uk
No mobile number

Dr Ezra Tolquist FRCS (please put FRCS in small font) - Name
Hair Restoration Surgeon - Job Title
drtolquist@formsculptors-example.co.uk
No mobile number

Colors
cedeec
85abd2
0655a3

Requirements
Must have
• The logo needs to be in a metallic finish
• Text needs to be striking
• nice background
• butterfly watermark on the back

```html
<!DOCTYPE html>
<html lang="en">
<head>
<meta charset="utf-8">
<title>Form Sculptors Business Card</title>
<link href="https://fonts.googleapis.com/css2?family=Cinzel:wght@400;700&display=swap" rel="stylesheet">
<style>
  :root {
    --backdrop: #e4e5e7;
    --satin-black: #1b1b1c;
    --satin-black-soft: #262627;
    --accent-red: #e2411f;
    --accent-orange: #f29a2e;
    --brand-blue: #2f86c4;
    --brand-blue-deep: #0655a3;
    --silver: #d9dadc;
    --service-white: #e8e8e8;
  }
  * { margin: 0; padding: 0; box-sizing: border-box; }
  html, body {
    width: 1200px; height: 720px; overflow: hidden;
    background: var(--backdrop);
  }
  .canvas { position: relative; width: 1200px; height: 720px; }
  .card {
    position: absolute; top: 205px;
    width: 540px; height: 309px;
    background: linear-gradient(135deg, var(--satin-black-soft), var(--satin-black));
    font-family: "Cinzel", serif;
    overflow: hidden;
  }
  .card--front { left: 40px; }
  .card--back { left: 620px; }

  .front-art { position: absolute; right: 0; top: 0; width: 270px; height: 309px; }

  .wordmark {
    position: absolute; left: 21px; top: 44px;
    font-size: 22px; font-weight: 400; color: var(--brand-blue);
    letter-spacing: 0.5px;
  }
  .holder-name {
    position: absolute; left: 21px; top: 104px;
    font-size: 16px; font-weight: 700; color: var(--accent-red);
  }
  .holder-title {
    position: absolute; left: 21px; top: 123px;
    font-size: 12px; color: var(--brand-blue);
  }
  .address {
    position: absolute; left: 21px; top: 158px;
    font-size: 11.5px; line-height: 15.5px; color: var(--brand-blue);
  }
  .contacts {
    position: absolute; left: 21px; top: 221px; list-style: none;
    font-size: 11.5px; line-height: 15.5px; color: var(--brand-blue);
  }
  .contacts li { display: flex; align-items: center; gap: 12px; }
  .contacts svg { width: 12px; height: 11px; flex: none; }

  .back-wordmark {
    position: absolute; left: 0; right: 0; top: 112px; text-align: center;
    font-size: 30px; font-weight: 400; color: var(--silver);
    letter-spacing: 0.5px;
  }
  .services {
    position: absolute; left: 0; right: 0; top: 217px; list-style: none;
    text-align: center; font-size: 12px; line-height: 15.5px;
    color: var(--service-white);
  }
</style>
</head>
<body>
<main class="canvas">
  <section class="card card--front" aria-label="Card front">
    <svg class="front-art" viewBox="0 0 270 309" role="img" aria-label="Large orange and blue butterfly brand artwork">
      <defs>
        <linearGradient id="artGradient" x1="0" y1="0" x2="1" y2="0">
          <stop offset="0" stop-color="#1b1b1c" stop-opacity="0"/>
          <stop offset="0.3" stop-color="#e8612a"/>
          <stop offset="0.55" stop-color="#2f86c4"/>
          <stop offset="1" stop-color="#f29a2e"/>
        </linearGradient>
      </defs>
      <rect width="270" height="309" fill="url(#artGradient)"/>
    </svg>

    <div class="wordmark">Form Sculptors</div>
    <div class="holder-name">Calvert Osterlund</div>
    <div class="holder-title">Chief Executive</div>
    <address class="address" style="font-style:normal">
      The London Farrowmere Clinic<br>
      14 Farrowmere Lane | London |<br>
      W1X 4QP Off Quenby Street
    </address>
    <ul class="contacts">
      <li><svg viewBox="0 0 12 11"><path d="M1 4h10v6H1z M2 4 Q6 0 10 4" fill="#e2411f"/></svg>+44 (0)207 946 0321</li>
      <li><svg viewBox="0 0 12 11"><rect x="3" y="0.5" width="6" height="10" rx="1" fill="none" stroke="#e2411f"/></svg>+44 (0)7700 900 147</li>
      <li><svg viewBox="0 0 12 11"><rect x="0.5" y="1.5" width="11" height="8" fill="#e2411f"/><path d="M0.5 1.5 6 6 11.5 1.5" fill="none" stroke="#1b1b1c"/></svg>calvert@formsculptors-example.co.uk</li>
      <li><svg viewBox="0 0 12 11"><rect x="0.5" y="1" width="11" height="7" fill="none" stroke="#e2411f"/><path d="M4 10h4" stroke="#e2411f"/></svg>www.formsculptors-example.co.uk</li>
    </ul>
  </section>

  <section class="card card--back" aria-label="Card back">
    <div class="back-wordmark">Form Sculptors</div>
    <ul class="services">
      <li>Hair Restoration surgery</li>
      <li>Hair Loss treatments</li>
      <li>Breast surgery Rhinoplasty Pulvix</li>
      <li>Liposuction Fat Grafting Lumaxin &amp; Fillers</li>
    </ul>
  </section>
</main>
</body>
</html>
```